Business Card Design

It's an investment advisory service for individuals with all there investment needs. Also financial consulting to businesses and governmental agencies on retirement plans etc. It's personalized not commoditized help. Should show strength, knowledge and money orientation.

Reason: Will be out of town setting up office.

Reason: waiting for the 2/3rds of group to vote

Reason: only half the votes are in, I'm calling and getting verbals, but at this time we are down to 2 designs.

Industry/Entity Type

Investment

Contact Information for Business Card

B. Rel K. Financial Consulting and Wealth Management, Berislav Mike Holcek, 5172 Pasadena Loma Verde, San Diego, CA 94417-6381, Registered Investment Advisor

Requirements
Nice to have
• Something money oriented

```html
<!DOCTYPE html>
<html lang="en">
<head>
<meta charset="utf-8">
<title>B. Rel K. Financial Consulting – Business Card</title>
<link rel="stylesheet" href="https://fonts.googleapis.com/css2?family=Baloo+2:wght@700&family=Lato:wght@400&family=Rokkitt:wght@800&display=swap">
<style>
  :root {
    --stage: #2b2b2b;
    --card-green: #6cc04a;
    --card-white: #ffffff;
    --name-blue: #2f3aa8;
    --brand-red: #ec2227;
    --text-dark: #1e1e1e;
    --coin-gold: #e8b923;
    --coin-deep: #c8901a;
  }
  * { box-sizing: border-box; margin: 0; padding: 0; }
  html, body { width: 1200px; height: 900px; overflow: hidden; background: var(--stage); }
  .canvas { position: relative; width: 1200px; height: 900px; display: flex; align-items: center; justify-content: center; }
  .card {
    position: relative; width: 1000px; height: 580px; overflow: hidden;
    background: var(--card-green);
    font-family: "Lato", sans-serif; color: var(--text-dark);
  }
  .card__sweep { position: absolute; inset: 0; width: 100%; height: 100%; }
  .card__holder {
    position: absolute; top: 46px; right: 50px;
    font-family: "Rokkitt", serif; font-weight: 800; font-size: 40px; line-height: 1.2; color: var(--name-blue);
  }
  .brand-mark {
    position: absolute; top: 104px; left: 40px;
    display: flex; align-items: center; gap: 10px;
  }
  .brand-mark__dot { width: 18px; height: 18px; border-radius: 50%; background: var(--brand-red); flex: none; }
  .brand-mark__name {
    font-family: "Lato", sans-serif; font-weight: 400; font-size: 26px; line-height: 1; color: var(--brand-red);
  }
  .card__company {
    position: absolute; top: 168px; left: 200px; width: 580px; text-align: center;
    font-family: "Baloo 2", sans-serif; font-weight: 700; font-size: 40px; line-height: 1.15; color: var(--brand-red);
  }
  .card__role {
    position: absolute; top: 280px; left: 255px;
    font-size: 29px; line-height: 1.2; letter-spacing: 0.3px;
  }
  .card__illustration {
    position: absolute; left: 40px; top: 330px; width: 360px; height: 220px;
    border-radius: 14px;
    background: radial-gradient(ellipse at 40% 60%, #ffe27a 0%, var(--coin-gold) 45%, var(--coin-deep) 100%);
  }
  .contact { position: absolute; left: 470px; top: 370px; font-size: 27px; line-height: 1.35; font-style: normal; }
  .contact__row { display: flex; align-items: flex-start; gap: 12px; }
  .contact__row--indent { padding-left: 32px; }
  .contact__icon { width: 20px; height: 26px; margin-top: 6px; fill: var(--text-dark); flex: none; }
</style>
</head>
<body>
<main class="canvas">
  <article class="card">
    <svg class="card__sweep" viewBox="0 0 1000 580" aria-hidden="true">
      <defs>
        <linearGradient id="sweepFade" x1="0" y1="0" x2="1" y2="0">
          <stop offset="0" stop-color="#ffffff"/>
          <stop offset="0.45" stop-color="#ffffff"/>
          <stop offset="1" stop-color="#6cc04a"/>
        </linearGradient>
      </defs>
      <path d="M0 0 H520 C300 60 120 250 30 580 H0 Z" fill="url(#sweepFade)"/>
    </svg>

    <h1 class="card__holder">Berislav Mike Holcek</h1>

    <div class="brand-mark">
      <span class="brand-mark__dot"></span>
      <span class="brand-mark__name">Holcek Advisory</span>
    </div>

    <h2 class="card__company">B. Rel K. Financial Consulting<br>&amp; Wealth Management</h2>
    <p class="card__role">Registered Investment Advisor</p>

    <div class="card__illustration" role="img" aria-label="Stacks of gold coins with a rising golden arrow"></div>

    <address class="contact">
      <div class="contact__row">
        <svg class="contact__icon" viewBox="0 0 20 26" aria-hidden="true"><path d="M10 0C4.5 0 0 4.3 0 9.7 0 16.5 10 26 10 26s10-9.5 10-16.3C20 4.3 15.5 0 10 0zm0 13.5a3.8 3.8 0 1 1 0-7.6 3.8 3.8 0 0 1 0 7.6z"/></svg>
        <span>5172 Pasadena Loma Verde,</span>
      </div>
      <div class="contact__row contact__row--indent"><span>San Diego, CA 94417-6381</span></div>
      <div class="contact__row">
        <svg class="contact__icon" viewBox="0 0 20 26" aria-hidden="true"><path d="M4 4c1-1 2.2-1 3 0l2.2 3c.6.9.5 2-.3 2.7L7.6 10.8c1 2.5 3 4.6 5.4 5.7l1.2-1.3c.7-.8 1.8-.9 2.7-.3l2.6 2c.9.7 1 1.9.2 2.8l-1.4 1.6c-1.2 1.3-3 1.7-4.6 1C7.5 19.9 3 15.3.9 9.5.3 7.9.8 6.1 2 5z"/></svg>
        <span>(619) 555-0147</span>
      </div>
    </address>
  </article>
</main>
</body>
</html>
```